Super elegant, crisp & clean Business card design required

We recently upgraded our branding - which is on our website - talvendoraphoto.com

I would like a simple, yet elegant, clean business card design please.

The font of my logo is Cinzel - and because of the natural colour - it's best to have this on a black background.

I would like to have the back of the business card - with simply my logo.

PLEASE DO NOT SUBMIT A COMPLICATED / UNCLEAN DESIGN

Industry/Entity Type

Business

Contact Information for Business Card

Talven Doroshko Photography

Font styles to use
Other font styles liked:
• Cinzel

Requirements
Must have
• A backpage with nothing but my logo
• Simple design - stands out
Should not have
• Colour that dont align with my logo
• Over complicated '/ non symmetrical design

```html
<!DOCTYPE html>
<html lang="en">
<head>
<meta charset="utf-8">
<title>Talven Doroshko Photography — Business Card</title>
<link rel="stylesheet" href="https://fonts.googleapis.com/css2?family=Cinzel:wght@400;700&display=swap">
<style>
  :root {
    --card-black: #070707;
    --card-glow: #151515;
    --gold: #8d7a5c;
    --gold-label: #94805f;
    --gold-value: #7f6f56;
    --text-shadow: rgba(0, 0, 0, 0.9);
  }
  * { margin: 0; padding: 0; box-sizing: border-box; }
  html, body {
    width: 1200px;
    height: 667px;
    overflow: hidden;
    background: var(--card-black);
  }
  .card {
    position: relative;
    width: 1200px;
    height: 667px;
    overflow: hidden;
    background:
      radial-gradient(ellipse 620px 520px at 320px 260px, var(--card-black) 0%, transparent 70%),
      linear-gradient(100deg, var(--card-black) 0%, #0c0c0c 55%, var(--card-glow) 100%);
    font-family: "Cinzel", serif;
    border: 1px solid #1c1c1c;
  }
  .brand {
    position: absolute;
    left: 104px;
    top: 140px;
    width: 440px;
    text-align: center;
    color: var(--gold);
  }
  .brand__mark {
    display: block;
    margin: 0 auto 34px;
    width: 118px;
    height: 118px;
  }
  .brand__name {
    font-size: 36px;
    font-weight: 400;
    letter-spacing: 0.02em;
    line-height: 1;
  }
  .brand__tagline {
    margin-top: 12px;
    font-size: 36px;
    font-weight: 400;
    letter-spacing: 0.02em;
    line-height: 1;
  }
  .contact {
    position: absolute;
    right: 106px;
    top: 310px;
    text-align: right;
    list-style: none;
  }
  .contact__item + .contact__item { margin-top: 48px; }
  .contact__label {
    display: block;
    font-size: 21px;
    font-weight: 700;
    color: var(--gold-label);
    letter-spacing: 0.01em;
    line-height: 1.2;
    text-shadow: 0 3px 8px var(--text-shadow);
  }
  .contact__value {
    display: block;
    margin-top: 4px;
    font-size: 24px;
    font-weight: 400;
    color: var(--gold-value);
    line-height: 1.2;
    text-shadow: 0 4px 10px var(--text-shadow);
  }
</style>
</head>
<body>
  <main class="card">
    <div class="brand">
      <svg class="brand__mark" viewBox="0 0 118 118" aria-hidden="true">
        <circle cx="59" cy="59" r="57" fill="none" stroke="var(--gold)" stroke-width="2"/>
      </svg>
      <p class="brand__name">Talven Doroshko</p>
      <p class="brand__tagline">Photography</p>
    </div>

    <ul class="contact">
      <li class="contact__item">
        <span class="contact__label">Phone Number</span>
        <span class="contact__value">07700 900123</span>
      </li>
      <li class="contact__item">
        <span class="contact__label">Website</span>
        <span class="contact__value">talvendoraphoto.com</span>
      </li>
      <li class="contact__item">
        <span class="contact__label">Email Address</span>
        <span class="contact__value">mail@talvendoraphoto.com</span>
      </li>
    </ul>
  </main>
</body>
</html>
```